Business Card Design

Business Card for professional consulting firm working with large financial institutions.

Target Market(s)

Executive buyers

Industry/Entity Type

Banking

Contact Information for Business Card

Mild creativity wanted. Not boring, but do elaborate artwork.

Font styles to use
Serif
Sans Serif

Colors

Designer to choose colors to be used in the design.

Requirements
Must have
• Standard business card features - company name, individual name, telephone, website, email, locations.
Nice to have
• Two colors
Should not have
• too many colors, fancy printing, cartoons.

```html
<!DOCTYPE html>
<html lang="en">
<head>
<meta charset="utf-8">
<title>k7advisory business card</title>
<link rel="stylesheet" href="https://fonts.googleapis.com/css2?family=Roboto:wght@400;500&family=Roboto+Condensed:wght@700&display=swap">
<style>
  :root {
    --backdrop: #2b2b2b;
    --card-front: #f3f3f3;
    --card-back: #c2c2c2;
    --ink: #111111;
    --ink-soft: #3a3a3a;
    --ink-muted: #a5a5a5;
    --rule: #6a6a6a;
    --band: #000000;
    --paper-white: #ffffff;
  }
  * { margin: 0; padding: 0; box-sizing: border-box; }
  html, body {
    width: 1200px; height: 960px; overflow: hidden;
    background: var(--backdrop);
    font-family: "Roboto", Arial, sans-serif;
  }
  .canvas { position: relative; width: 1200px; height: 960px; }

  .card {
    position: absolute; width: 600px; height: 343px;
    box-shadow: 0 3px 8px rgba(0,0,0,0.45);
  }
  .card--front { left: 314px; top: 113px; background: var(--card-front); }
  .card--back { left: 311px; top: 472px; background: var(--card-back); }

  .brand-name {
    position: absolute; font-family: "Roboto", Arial, sans-serif;
    font-weight: 400; letter-spacing: 0.5px; white-space: nowrap;
  }
  .card--front .brand-name { right: 70px; top: 56px; font-size: 28px; color: var(--ink-soft); }
  .card--back .brand-name {
    left: 0; right: 0; top: 140px; text-align: center;
    font-size: 40px; color: var(--paper-white);
  }

  .name-marker { position: absolute; left: 0; top: 192px; width: 9px; height: 47px; background: var(--ink); }
  .person-name {
    position: absolute; left: 32px; top: 196px;
    font-family: "Roboto Condensed", "Arial Narrow", sans-serif;
    font-weight: 700; font-size: 23px; color: var(--ink); line-height: 1;
  }
  .person-title {
    position: absolute; left: 32px; top: 223px;
    font-family: "Roboto", Arial, sans-serif; font-weight: 500;
    font-size: 15px; color: var(--ink-muted); line-height: 1;
  }
  .divider { position: absolute; left: 32px; top: 249px; width: 533px; height: 1px; background: var(--rule); }

  .contact-list { position: absolute; left: 32px; top: 263px; list-style: none; }
  .contact-list li {
    display: flex; align-items: center; height: 19px;
    font-size: 14px; color: var(--ink-soft);
  }
  .contact-list svg { width: 13px; height: 13px; margin-right: 8px; fill: var(--ink); }

  .address {
    position: absolute; right: 33px; top: 263px; text-align: right;
    font-style: normal; font-size: 14px; line-height: 19px; color: var(--ink-soft);
  }

  .web-band {
    position: absolute; left: 0; top: 275px; width: 600px; height: 29px;
    background: var(--band); color: var(--paper-white);
    font-size: 14px; letter-spacing: 6.4px; text-align: center; line-height: 29px;
  }
</style>
</head>
<body>
<main class="canvas">
  <section class="card card--front" aria-label="Card front">
    <div class="brand-name">k7advisory</div>
    <div class="name-marker"></div>
    <h1 class="person-name">DANIEL HART</h1>
    <p class="person-title">CEO/FOUNDER</p>
    <div class="divider"></div>
    <ul class="contact-list">
      <li><svg viewBox="0 0 16 16" aria-hidden="true"><path d="M3.5 1.5l2.6 0 1.2 3.4-1.7 1.2c.8 1.7 2.1 3 3.8 3.8l1.2-1.7 3.4 1.2v2.6c0 .8-.7 1.5-1.5 1.5C6.9 13.5 2 8.6 2 3c0-.8.7-1.5 1.5-1.5z"/></svg>555 014 2290</li>
      <li><svg viewBox="0 0 16 16" aria-hidden="true"><path d="M1 3h14v1.2L8 8.6 1 4.2z M1 5.6l7 4.4 7-4.4V13H1z"/></svg>info@k7advisory.com</li>
      <li><svg viewBox="0 0 16 16" aria-hidden="true"><circle cx="8" cy="8" r="6.8"/><path d="M5 4.5c1.2.3 1.8 1.4 1.2 2.5-.5.9.6 1.6 1.4 2.2.7.6.2 2-.4 3M10.5 3.2c-.4 1 .3 1.8 1.3 2" stroke="#f3f3f3" stroke-width="1.2" fill="none"/></svg>www.k7advisory.com</li>
    </ul>
    <address class="address">k7advisory<br>1420 Harbor View Road<br>Juneau, Alaska 99801</address>
  </section>

  <section class="card card--back" aria-label="Card back">
    <div class="brand-name">k7advisory</div>
    <div class="web-band">www.k7advisory.com</div>
  </section>
</main>
</body>
</html>
```